New Business Card for our Indoor Golf Training Facility

We are looking for designs for a new business card for our indoor golf training facility. Attached is our logo, our logo with our slogan, and here is our elevator pitch (What makes us different from the others) not sure if all the info will fit on one card, maybe you can condense the elevator pitch? here is the info

Elevator Pitch
We work with serious golfers and those that want to be serious golfers…
to make you better, faster, at all phases of the game…
We use the same state-of-the-art technology as professional golfers…
which produces data sets that shows your improvement in real time.
Our facility is available 24/7 to our members, which allows you to improve on your time.

our website: www.birchpinlinks.com

Target Market(s)

Golfers

Font styles to use
Serif
Sans Serif

Colors
ec1f27
f59195
fbd4d5
919191
d3d3d3
1b1b1b

Requirements
Must have
• our logo or our logo with the slogan, elevator pitch (can be condensed or shortened)

```html
<!DOCTYPE html>
<html lang="en">
<head>
<meta charset="utf-8">
<title>Birch Pin Links — Business Card</title>
<link rel="stylesheet" href="https://fonts.googleapis.com/css2?family=Roboto:ital,wght@0,300;0,400;0,700;0,900;1,400&display=swap">
<style>
  :root {
    --brand-red: #ec1f27;
    --brand-pink: #f59195;
    --brand-blush: #fbd4d5;
    --mid-grey: #919191;
    --light-grey: #d3d3d3;
    --ink: #1b1b1b;
    --body-grey: #555555;
    --paper: #ffffff;
    --stage: #ecebea;
  }
  * { box-sizing: border-box; margin: 0; padding: 0; }
  html, body {
    width: 1200px; height: 911px; overflow: hidden;
    background: var(--stage);
    font-family: "Roboto", Arial, sans-serif;
  }
  .stage {
    width: 1200px; height: 911px;
    display: flex; flex-direction: column; align-items: center; justify-content: center;
    gap: 36px;
  }
  .card {
    width: 680px; height: 389px;
    border-radius: 26px;
    position: relative;
    overflow: hidden;
    box-shadow: 0 6px 18px rgba(0,0,0,0.15);
  }
  /* Front */
  .card--front { background: var(--brand-red); color: var(--paper); }
  .card__frame {
    position: absolute; inset: 14px;
    border: 2px solid var(--paper);
    border-radius: 18px;
  }
  .front__mark {
    position: absolute; right: 70px; top: 62px;
    font-weight: 900; font-size: 40px; letter-spacing: 0.5px;
    color: var(--paper);
  }
  .front__contact {
    position: absolute; left: 52px; bottom: 44px;
  }
  .person__name { font-weight: 700; font-size: 30px; line-height: 1.1; }
  .person__role { font-weight: 300; font-size: 18px; margin-bottom: 16px; }
  .address { font-weight: 300; font-size: 17px; line-height: 1.35; margin-bottom: 10px; }
  .contact-list { list-style: none; font-weight: 300; font-size: 17px; line-height: 1.5; }
  .contact-list li { display: flex; align-items: center; gap: 10px; }
  .contact-list svg { width: 15px; height: 15px; fill: var(--paper); flex: none; }
  /* Back */
  .card--back { background: var(--paper); color: var(--ink); text-align: center; }
  .logo-row {
    margin-top: 40px;
    display: flex; align-items: center; justify-content: center; gap: 14px;
  }
  .logo-row__dot {
    width: 50px; height: 50px; border-radius: 50%;
    border: 4px solid var(--brand-red);
  }
  .logo-row__name { font-weight: 900; font-size: 46px; color: var(--brand-red); }
  .slogan { font-weight: 300; font-size: 19px; color: var(--brand-red); margin-top: 2px; }
  .pitch__title {
    margin-top: 20px;
    font-weight: 700; font-size: 21px; color: var(--brand-red); letter-spacing: 0.5px;
  }
  .pitch__body {
    margin: 8px auto 0; width: 620px;
    font-style: italic; font-size: 14.5px; line-height: 1.55; color: var(--body-grey);
  }
  .social { display: flex; justify-content: center; gap: 8px; margin-top: 14px; }
  .social span { width: 18px; height: 18px; border-radius: 50%; background: var(--brand-red); }
</style>
</head>
<body>
<main class="stage">
  <section class="card card--front">
    <div class="card__frame"></div>
    <div class="front__mark">Birch Pin Links</div>
    <div class="front__contact">
      <h1 class="person__name">Daniel Reyes</h1>
      <p class="person__role">CEO/Founder</p>
      <p class="address">1840 Larkfield Rd, Unit B3<br>Maplewood, OH 45100</p>
      <ul class="contact-list">
        <li><svg viewBox="0 0 24 24"><path d="M6.6 10.8a15 15 0 0 0 6.6 6.6l2.2-2.2a1 1 0 0 1 1-.25 11.4 11.4 0 0 0 3.6.57 1 1 0 0 1 1 1V20a1 1 0 0 1-1 1A17 17 0 0 1 3 4a1 1 0 0 1 1-1h3.5a1 1 0 0 1 1 1c0 1.25.2 2.45.57 3.57a1 1 0 0 1-.25 1z"/></svg>555-201-7788</li>
        <li><svg viewBox="0 0 24 24"><path d="M2 5h20v14H2z M2 5l10 8 10-8" stroke="#ec1f27" stroke-width="1.5"/></svg>info@birchpinlinks.com</li>
        <li><svg viewBox="0 0 24 24"><circle cx="12" cy="12" r="10"/></svg>birchpinlinks.com</li>
      </ul>
    </div>
  </section>

  <section class="card card--back">
    <div class="logo-row">
      <span class="logo-row__dot"></span>
      <span class="logo-row__name">Birch Pin Links</span>
    </div>
    <p class="slogan">Swing Smarter. Play Sharper. Go Further.</p>
    <h2 class="pitch__title">ELEVATOR PITCH:</h2>
    <p class="pitch__body">
      We coach committed players and anyone ready to commit to their game…<br>
      to help you improve quickly, in every part of the round…<br>
      Our bays run the same launch-monitor systems the tour players trust…<br>
      so every session logs the numbers that track your progress live.<br>
      Members get round-the-clock access, so you can practice whenever it suits you.
    </p>
    <div class="social"><span></span><span></span></div>
  </section>
</main>
</body>
</html>
```